Corporate Design für Apotheke
Zielgruppe
Gesundheitswesen, Apotheke Zielgruppe kranke Menschen aber auch 'shopper'.
Aufgabenstellung
Das alte Logo ist leider viel zu filigran. Bei verschiedenen Druck kommt es oft nicht raus. Früher war das Logo eckig, es wurde vor Jahren mal als rund modernisiert.
Bin aber offen für alles.
Apotheke sollte grundsätzlich mit den Werten Seriosität, Vertrauen , und in unserem Fall auch Exklusivität, Premium- Segment verbunden werden. Im Anhang unser altes Logo. Ich bin zum ersten mal hier und freue mich auf kreative Vorschläge

```html
<!DOCTYPE html>
<html lang="de">
<head>
<meta charset="utf-8">
<title>Talgrund Apotheke – Visitenkarten</title>
<link rel="stylesheet" href="https://fonts.googleapis.com/css2?family=Montserrat:wght@700&family=Jost:wght@400;500&family=Caveat:wght@400&display=swap">
<style>
  :root {
    --bg: #e4e4e4;
    --card-white: #ffffff;
    --card-green: #57b95c;
    --green-dark: #2a7a4a;
    --green-light: #4cae50;
    --text-light: #ffffff;
    --rule: rgba(255,255,255,0.9);
  }
  * { margin: 0; padding: 0; box-sizing: border-box; }
  html, body { width: 869px; height: 1200px; overflow: hidden; }
  body {
    background: radial-gradient(ellipse at 50% 45%, #f1f1f1 0%, var(--bg) 75%);
    position: relative;
    font-family: "Jost", sans-serif;
  }
  .card {
    position: absolute;
    box-shadow: 0 2px 6px rgba(0,0,0,0.12);
  }
  .card--front {
    left: 142px; top: 170px; width: 592px; height: 336px;
    background: var(--card-white);
  }
  .card--back {
    left: 139px; top: 596px; width: 597px; height: 339px;
    background: var(--card-green);
    color: var(--text-light);
  }
  .brand-mark {
    position: absolute;
    left: 255px; top: 67px; width: 82px; height: 82px;
    border: 3px solid var(--green-dark);
    border-radius: 50%;
  }
  .brand-name {
    font-family: "Montserrat", sans-serif;
    font-weight: 700;
    letter-spacing: 3px;
    white-space: nowrap;
  }
  .card--front .brand-name {
    position: absolute; left: 0; right: 0; top: 172px;
    text-align: center; font-size: 27px; color: var(--green-dark);
  }
  .tagline {
    font-family: "Caveat", cursive;
    white-space: nowrap;
  }
  .card--front .tagline {
    position: absolute; left: 0; right: 0; top: 212px;
    text-align: center; font-size: 31px; color: var(--green-light);
  }
  .card--back .brand-name {
    position: absolute; left: 55px; top: 50px;
    font-size: 25px; color: var(--text-light);
  }
  .divider {
    position: absolute; left: 55px; top: 99px;
    width: 485px; height: 2px; background: var(--rule);
  }
  .address {
    position: absolute; left: 55px; top: 127px;
    font-size: 18px; letter-spacing: 0.3px;
  }
  .contact {
    position: absolute; left: 55px; top: 171px;
    font-size: 18px; line-height: 26px;
  }
  .contact dt { float: left; clear: left; width: 58px; font-weight: 500; }
  .contact dd { margin-left: 58px; }
  .card--back .tagline {
    position: absolute; left: 114px; top: 268px;
    font-size: 29px;
  }
</style>
</head>
<body>
  <section class="card card--front" aria-label="Visitenkarte Vorderseite">
    <div class="brand-mark" aria-hidden="true"></div>
    <h1 class="brand-name">TALGRUND APOTHEKE</h1>
    <p class="tagline">Gesundheit mitten in Tannhofen</p>
  </section>

  <section class="card card--back" aria-label="Visitenkarte Rückseite">
    <h2 class="brand-name">TALGRUND APOTHEKE</h2>
    <div class="divider"></div>
    <p class="address">Musterstraße 1 | 79999 Tannhofen</p>
    <dl class="contact">
      <dt>Fon:</dt><dd>012 987 44 10</dd>
      <dt>Web:</dt><dd>talgrund-apotheke.de</dd>
      <dt>Mail:</dt><dd>info@talgrund-apotheke.de</dd>
    </dl>
    <p class="tagline">… Wir sind für Sie da!</p>
  </section>
</body>
</html>
```